Whitcombe Business Card Design

The name of the business is Dario Whitcombe, CPA LLC
The service that we offer is Accounting, Tax & Consulting Services. I need it to have the following items:
Dario Whitcombe, Principal
Phone Number
Email Address
Physical Address

I have attached the company logo, one in black and one in white. Please provide a design in black background and the other in white background. Please include "Accounting, Tax & Consulting Services". I want the business card to be clean and very professional.

```html
<!DOCTYPE html>
<html lang="en">
<head>
<meta charset="UTF-8">
<title>Dario Whitcombe, CPA LLC – Business Card</title>
<link href="https://fonts.googleapis.com/css2?family=Montserrat:wght@500&family=Roboto:wght@400;500;700&display=swap" rel="stylesheet">
<style>
  :root {
    --backdrop: #d9d9d9;
    --card: #ffffff;
    --brand-red: #9b1b1e;
    --ink: #3a3a3c;
    --muted: #8c8c8c;
    --pattern-light: #f3eeee;
    --pattern-mid: #ebe4e4;
  }
  * { box-sizing: border-box; margin: 0; padding: 0; }
  html, body {
    width: 1200px; height: 900px; overflow: hidden;
    background: var(--backdrop);
    font-family: "Roboto", Arial, sans-serif;
  }
  .stage { position: relative; width: 1200px; height: 900px; }

  .card {
    position: absolute;
    background: var(--card);
    box-shadow: 0 3px 10px rgba(0,0,0,0.22);
  }

  /* Front card */
  .card--front { left: 237px; top: 43px; width: 687px; height: 392px; overflow: hidden; }
  .front-texture {
    position: absolute; inset: 0;
    background: linear-gradient(135deg, var(--pattern-light), var(--pattern-mid));
  }
  .brand-mark {
    position: absolute;
    background: var(--ink);
  }
  .brand-mark--front { left: 270px; top: 83px; width: 144px; height: 144px; }
  .front-brand {
    position: absolute; left: 0; right: 0; top: 250px;
    text-align: center;
  }
  .front-brand__name {
    font-family: "Roboto", Arial, sans-serif;
    font-weight: 500; font-size: 42px; color: var(--ink);
    letter-spacing: 1px; text-transform: uppercase; line-height: 1;
  }
  .front-brand__tagline {
    margin-top: 10px;
    font-family: "Montserrat", Arial, sans-serif;
    font-weight: 500; font-size: 28px; color: var(--muted);
    letter-spacing: 3.6px; line-height: 1;
  }

  /* Back card */
  .card--back { left: 233px; top: 460px; width: 701px; height: 401px; }
  .brand-mark--back { left: 17px; top: 20px; width: 94px; height: 94px; }
  .back-brand { position: absolute; left: 18px; top: 122px; }
  .back-brand__name {
    font-family: "Roboto", Arial, sans-serif;
    font-weight: 500; font-size: 18px; color: var(--ink);
    text-transform: uppercase; letter-spacing: 0.4px; line-height: 1;
  }
  .back-brand__tagline {
    margin-top: 5px;
    font-family: "Montserrat", Arial, sans-serif;
    font-weight: 500; font-size: 12px; color: var(--muted);
    letter-spacing: 1.5px; text-transform: uppercase; line-height: 1;
  }

  .person { position: absolute; right: 16px; top: 18px; text-align: right; }
  .person__name { font-weight: 700; font-size: 27px; color: var(--ink); line-height: 1.1; }
  .person__role { font-weight: 500; font-size: 19px; color: var(--brand-red); margin-top: 3px; }

  .services {
    position: absolute; left: 18px; right: 16px; top: 212px;
    font-weight: 700; font-size: 24px; color: var(--brand-red);
    letter-spacing: 4.7px; white-space: nowrap; line-height: 1;
    padding-bottom: 10px; border-bottom: 2px solid var(--ink);
  }

  .contact {
    position: absolute; display: flex; align-items: center; gap: 12px;
    font-size: 22px; color: var(--ink); line-height: 1.3;
  }
  .contact svg { flex: none; }
  .contact--phone { left: 18px; top: 278px; }
  .contact--email { left: 18px; top: 322px; }
  .contact--address { left: 355px; top: 278px; align-items: flex-start; }
  .contact--address svg { margin-top: 1px; }
</style>
</head>
<body>
<div class="stage">

  <section class="card card--front">
    <div class="front-texture" role="img" aria-label="Faint repeating brand pattern background"></div>
    <div class="brand-mark brand-mark--front" role="img" aria-label="Company logo mark"></div>
    <div class="front-brand">
      <div class="front-brand__name">Dario Whitcombe, CPA LLC</div>
      <div class="front-brand__tagline">CERTIFIED PUBLIC ACCOUNTANT</div>
    </div>
  </section>

  <section class="card card--back">
    <div class="brand-mark brand-mark--back" role="img" aria-label="Company logo mark"></div>
    <div class="back-brand">
      <div class="back-brand__name">Dario Whitcombe, CPA LLC</div>
      <div class="back-brand__tagline">Certified Public Accountant</div>
    </div>

    <div class="person">
      <div class="person__name">Dario Whitcombe</div>
      <div class="person__role">Principal</div>
    </div>

    <div class="services">ACCOUNTING, TAX &amp; CONSULTING SERVICES</div>

    <div class="contact contact--phone">
      <svg width="34" height="34" viewBox="0 0 34 34" aria-hidden="true">
        <circle cx="17" cy="17" r="15.5" fill="none" stroke="#3a3a3c" stroke-width="2"/>
        <path d="M11.5 10.5c1-1 2-1 2.6 0l1.6 2.6c.4.7.2 1.4-.4 1.9l-1 .8c.8 1.900 2.2 3.400 4.1 4.300l.9-1c.5-.6 1.2-.7 1.9-.3l2.6 1.6c.9.6.9 1.6 0 2.5l-1 1c-1.3 1.2-3.7.6-6.6-1.9-3-2.6-4.7-5.7-4.7-7.6 0-.6.2-1.2.6-1.600z" fill="#9b1b1e"/>
      </svg>
      <span>(555) 014-0365</span>
    </div>

    <div class="contact contact--email">
      <svg width="34" height="34" viewBox="0 0 34 34" aria-hidden="true">
        <circle cx="17" cy="17" r="15.5" fill="none" stroke="#3a3a3c" stroke-width="2"/>
        <rect x="9" y="11.5" width="16" height="11" rx="1" fill="#9b1b1e"/>
        <path d="M9.5 12.5l7.5 6 7.5-6" fill="none" stroke="#fff" stroke-width="1.4"/>
      </svg>
      <span>info@whitcombe.com</span>
    </div>

    <div class="contact contact--address">
      <svg width="34" height="34" viewBox="0 0 34 34" aria-hidden="true">
        <circle cx="17" cy="17" r="15.5" fill="none" stroke="#3a3a3c" stroke-width="2"/>
        <path d="M17 8a6 6 0 0 0-6 6c0 4.5 6 11 6 11s6-6.5 6-11a6 6 0 0 0-6-6z" fill="#9b1b1e"/>
        <circle cx="17" cy="14" r="2.3" fill="#fff"/>
      </svg>
      <span>421, Address line goes here<br>45552, Country Name</span>
    </div>
  </section>

</div>
</body>
</html>
```